Wedding filmmaker needs artistic business card design - brightwaterreels.ca

We are high end wedding filmmakers in a major market who produce cinematic wedding films. We require a business card design that communicates our quality, artistry, and professionalism yet looks progressive and friendly. Colors and design should skew appeal more to the bride-to-be who is usually the decision maker but not be overtly feminine per se. This means generally light pastel shades of ivory, purple, pink, yellow, as examples.
We already have a name logo established: the words "Brightwater Reels" in the font Great Vibes. Designs must use Kraft natural cardstock as the print stock and am leaning heavily toward our name logo in white, but I am open to black as well. Please design any color elements with spot white underneath where possible.
Do not try to compliment or take inspiration from our website design. Treat the card design as a separate stand alone.
Thank you so much for your hard work!

Target Market(s)

Affluent couples spending $50,000+ on their wedding

Industry/Entity Type

Progressive

Contact Information for Business Card

Peter Brightwater
Producer
905-482-7139
www.brightwaterreels.ca
peter@brightwaterreels.ca
twitter @brightwater287

Font styles to use
Serif
Sans Serif

Requirements
Must have
• - Brightwater Reels name logo (reference GIF uploaded for reference only) and catch phrase: Breathtaking wedding films (I'm open to capitalizing all three words, or just first, or all in small caps). I favor logo, and catch phrase on front of card and my contact details on the other side but if you feel strongly about a different design, go for it!
• - Design must be submitted shown on Kraft natural cardstock NOT WHITE cardstock, If you're not familiar with Kraft, this is what it looks like: http://www.quillandlatchjournal.com/wp-content/uploads/2013/07/il_570xN.382745196_kq3m.jpg
Nice to have
• - An original graphic element (eg. movie reel, bouquet, confetti, etc.) that compliments the name logo but is subtle and discreet, doesn't overpower or entangle it.
• -Great use of balance, composition, negative space, etc. I like clean tasteful design
Should not have
• -Lousy boring clip art.
• -Graphic elements, fonts, or color palette from our website
• -White cardstock background
• -designs you have previously submitted for other contests
• -Bold dark colors (eg. red, orange navy blue, etc.)
• -High tech futuristic designs like you'd create for a software company

```html
<!DOCTYPE html>
<html lang="en">
<head>
<meta charset="utf-8">
<title>Brightwater Reels – Business Card</title>
<link rel="stylesheet" href="https://fonts.googleapis.com/css2?family=Exo+2:wght@400;500&display=swap">
<style>
  :root {
    --backdrop: #efe9e0;
    --kraft-top: #c9a57a;
    --kraft-bottom: #b89066;
    --ink: #3e2a1c;
    --ink-soft: #4d3626;
    --logo: #ffffff;
    --band: #f4ecdc;
    --band-edge: #e7c9d0;
    --band-text: #4d3626;
    --rule: #f6efe4;
  }
  * { margin: 0; padding: 0; box-sizing: border-box; }
  html, body {
    width: 1200px; height: 768px; overflow: hidden;
    background: var(--backdrop);
    font-family: "Exo 2", sans-serif;
  }
  .card {
    position: absolute; left: 100px; top: 94px;
    width: 1000px; height: 580px;
    border-radius: 34px; overflow: hidden;
    background: linear-gradient(180deg, var(--kraft-top), var(--kraft-bottom));
    box-shadow: 0 10px 30px rgba(60,40,20,.18);
    color: var(--ink);
  }
  .card__name {
    position: absolute; left: 42px; top: 180px;
    font-size: 28px; font-weight: 500; letter-spacing: 2px;
  }
  .card__role {
    position: absolute; left: 42px; top: 236px;
    font-size: 22px; font-weight: 500; color: var(--ink-soft);
  }
  .card__brand {
    position: absolute; right: 46px; top: 150px;
    text-align: right; color: var(--logo);
  }
  .card__logo {
    font-size: 54px; font-weight: 400; line-height: 1.1; white-space: nowrap;
  }
  .card__tagline {
    margin-top: 4px;
    font-size: 16px; font-weight: 500; letter-spacing: 3px;
    font-variant: small-caps; color: var(--logo);
  }
  .card__rule {
    position: absolute; left: 61px; top: 290px;
    width: 866px; height: 3px;
    background: linear-gradient(90deg, rgba(246,239,228,0), var(--rule) 20%, var(--rule) 75%, rgba(246,239,228,0));
  }
  .card__address {
    position: absolute; left: 42px; top: 374px;
    font-size: 22px; line-height: 34px; color: var(--ink-soft); font-style: normal;
  }
  .contact {
    position: absolute; right: 36px; top: 316px;
    list-style: none; text-align: right;
  }
  .contact__item {
    display: flex; justify-content: flex-end; align-items: center;
    gap: 14px; color: var(--ink); font-size: 20px; height: 46px;
  }
  .contact__item--phone { font-size: 21px; letter-spacing: 1.5px; }
  .contact__icon { width: 22px; height: 22px; fill: var(--ink-soft); flex: none; }
  .card__band { position: absolute; left: 0; bottom: 0; width: 1000px; height: 64px; }
  .card__band-url {
    position: absolute; left: 42px; bottom: 20px;
    font-size: 20px; font-weight: 500; color: var(--band-text); letter-spacing: .5px;
  }
</style>
</head>
<body>
  <article class="card">
    <h1 class="card__name">PETER BRIGHTWATER</h1>
    <p class="card__role">Producer</p>

    <div class="card__brand">
      <p class="card__logo">Brightwater Reels</p>
      <p class="card__tagline">Breathtaking Wedding Films</p>
    </div>

    <div class="card__rule"></div>

    <address class="card__address">
      214.6th floor,Quay<br>Millbrook Road KLM
    </address>

    <ul class="contact">
      <li class="contact__item contact__item--phone">905-482-7139
        <svg class="contact__icon" viewBox="0 0 24 24"><path d="M6.6 10.8a15 15 0 0 0 6.6 6.6l2.2-2.2c.3-.3.7-.4 1-.2 1.1.4 2.3.6 3.6.6.6 0 1 .4 1 1V20c0 .6-.4 1-1 1A17 17 0 0 1 3 4c0-.6.4-1 1-1h3.5c.6 0 1 .4 1 1 0 1.3.2 2.5.6 3.6.1.3 0 .7-.2 1z"/></svg>
      </li>
      <li class="contact__item">@brightwater287
        <svg class="contact__icon" viewBox="0 0 24 24"><path d="M12 2a10 10 0 1 0 5 18.7l-1-1.7A8 8 0 1 1 20 12v1a2 2 0 0 1-4 0V7h-2v1a5 5 0 1 0 .6 7A4 4 0 0 0 22 13v-1A10 10 0 0 0 12 2zm0 13a3 3 0 1 1 0-6 3 3 0 0 1 0 6z"/></svg>
      </li>
      <li class="contact__item">peter@brightwaterreels.ca
        <svg class="contact__icon" viewBox="0 0 24 24"><path d="M2 5h20v14H2zm2 2v.5l8 5.5 8-5.5V7zm0 3v7h16v-7l-8 5.5z"/></svg>
      </li>
      <li class="contact__item">www.brightwaterreels.ca
        <svg class="contact__icon" viewBox="0 0 24 24"><path d="M12 2a10 10 0 1 0 0 20 10 10 0 0 0 0-20zm7.9 9h-3.4a15 15 0 0 0-1.3-6.2A8 8 0 0 1 19.9 11zM12 4c.9 1.2 2.3 3.6 2.5 7h-5C9.7 7.6 11.1 5.2 12 4zM8.8 4.8A15 15 0 0 0 7.5 11H4.1a8 8 0 0 1 4.7-6.2zM4.1 13h3.4a15 15 0 0 0 1.3 6.2A8 8 0 0 1 4.1 13zM12 20c-.9-1.2-2.3-3.6-2.5-7h5c-.2 3.4-1.6 5.8-2.5 7zm3.2-.8a15 15 0 0 0 1.3-6.2h3.4a8 8 0 0 1-4.7 6.2z"/></svg>
      </li>
    </ul>

    <svg class="card__band" viewBox="0 0 1000 64" preserveAspectRatio="none" aria-hidden="true">
      <path d="M0 0H360C392 0 404 12 418 30V64H0Z" fill="var(--band)"/>
      <path d="M418 22H1000V64H418Z" fill="var(--band)"/>
      <path d="M360 0C394 0 406 14 420 34 L426 64" fill="none" stroke="var(--band-edge)" stroke-width="4"/>
    </svg>
    <p class="card__band-url">www.brightwaterreels.ca</p>
  </article>
</body>
</html>
```